Business Card for Multi-Brand Sportswear Company

We are looking for a business card which represents our company and the multiple brands within it.

The company: Fen Athletics (LTD)
The brands: Fen, TavaPuni, ElmStretch, Grit and Rain

Employees using these cards would be representing Fen Athletics, rather than any of the individual brands. You will see a current design within the uploaded files, to give some inspiration. The actual text of the brands is not necessary, but the logos should be on there is some format.

Our creative minds on this are stretched, so we are looking for someone to make this their own, and show us what a good business card should look like.

We may like to get these printed with spot gloss, so keep that in mind with your designs.

www.fenathletics.co.uk

Industry/Entity Type

Business

Contact Information for Business Card

Leo Pemberton-Hale
Operations Manager
(+44) 1632 960 418
Leo@fenathletics.co.uk
www.fenathletics.co.uk

Font styles to use
Sans Serif
Other font styles liked:
• Eurostile

Colors
ffffff

Requirements
Nice to have
• Dark (black) background

```html
<!DOCTYPE html>
<html lang="en">
<head>
<meta charset="utf-8">
<title>Fen Athletics – Business Card</title>
<link rel="stylesheet" href="https://fonts.googleapis.com/css2?family=Quicksand:wght@500;600;700&display=swap">
<style>
  :root {
    --backdrop: #8c8c8c;
    --card: #2b2a2a;
    --accent: #e52421;
    --white: #ffffff;
    --mark-grey: #5c5b5b;
    --brand-grey: #9a9a9a;
  }
  * { margin: 0; padding: 0; box-sizing: border-box; }
  html, body {
    width: 1200px; height: 854px; overflow: hidden;
    background: var(--backdrop);
    font-family: "Quicksand", sans-serif;
  }
  .card {
    position: absolute; top: 296px;
    width: 489px; height: 279px;
    background: var(--card);
    color: var(--white);
  }
  .card--front { left: 93px; }
  .card--back { left: 600px; }

  .divider {
    position: absolute; left: 258px; top: 0;
    width: 2px; height: 100%;
    background: var(--accent);
  }
  .wordmark {
    position: absolute;
    font-weight: 600; color: var(--mark-grey);
    white-space: nowrap; letter-spacing: 0.5px;
  }
  .card--front .wordmark { left: 18px; top: 106px; font-size: 29px; }
  .card--back .wordmark { left: 0; width: 100%; text-align: center; top: 90px; font-size: 52px; }

  .brand-row {
    position: absolute; display: flex; align-items: center;
    gap: 10px; white-space: nowrap;
    font-weight: 600; color: var(--brand-grey);
  }
  .card--front .brand-row { left: 18px; width: 230px; justify-content: center; top: 188px; font-size: 9.5px; }
  .card--back .brand-row { left: 0; width: 100%; justify-content: center; top: 222px; font-size: 12px; gap: 16px; }

  .person {
    position: absolute; right: 21px; top: 107px; text-align: right;
  }
  .person__name { font-size: 18.5px; font-weight: 600; letter-spacing: -0.3px; }
  .person__role { font-size: 15px; font-weight: 500; margin-top: 5px; }

  .contact {
    position: absolute; left: 241px; top: 184px;
    list-style: none;
  }
  .contact__item {
    display: flex; align-items: center; height: 17px; margin-bottom: 6px;
    font-size: 13.5px; font-weight: 500;
  }
  .contact__icon {
    width: 51px; height: 17px; border-radius: 3px;
    background: var(--accent);
    display: flex; align-items: center; justify-content: center;
    margin-right: 10px;
  }
  .contact__icon svg { width: 11px; height: 11px; }
</style>
</head>
<body>
  <section class="card card--front">
    <div class="divider"></div>
    <div class="wordmark">Fen Athletics</div>
    <div class="brand-row">
      <span>TavaPuni</span><span>Grit and Rain</span><span>Fen</span><span>ElmStretch</span>
    </div>
    <div class="person">
      <div class="person__name">Leo Pemberton-Hale</div>
      <div class="person__role">Operations Manager</div>
    </div>
    <ul class="contact">
      <li class="contact__item">
        <span class="contact__icon">
          <svg viewBox="0 0 24 24" fill="#fff"><path d="M6.6 10.8a15.1 15.1 0 0 0 6.6 6.6l2.2-2.2a1 1 0 0 1 1-.25 11.4 11.4 0 0 0 3.6.57 1 1 0 0 1 1 1V20a1 1 0 0 1-1 1A17 17 0 0 1 3 4a1 1 0 0 1 1-1h3.5a1 1 0 0 1 1 1c0 1.25.2 2.45.57 3.57a1 1 0 0 1-.25 1z"/></svg>
        </span>(+44) 1632 960 418
      </li>
      <li class="contact__item">
        <span class="contact__icon">
          <svg viewBox="0 0 24 24" fill="none" stroke="#fff" stroke-width="2.4"><rect x="3" y="5" width="18" height="14" rx="1.5"/><path d="M3 6l9 7 9-7"/></svg>
        </span>Leo@fenathletics.co.uk
      </li>
      <li class="contact__item">
        <span class="contact__icon">
          <svg viewBox="0 0 24 24" fill="none" stroke="#fff" stroke-width="2"><circle cx="12" cy="12" r="9"/><path d="M3 12h18M12 3c3 3 3 15 0 18M12 3c-3 3-3 15 0 18"/></svg>
        </span>www.fenathletics.co.uk
      </li>
    </ul>
  </section>

  <section class="card card--back">
    <div class="wordmark">Fen Athletics</div>
    <div class="brand-row">
      <span>TavaPuni</span><span>Grit and Rain</span><span>Fen</span><span>ElmStretch</span>
    </div>
  </section>
</body>
</html>
```